TA BRAMLEY BUSINESS CARD DESIGN PROJECT

We need to utilize our logo that was expertly created on PixelHarbor and now need to match this with a business card design.

```html
<!DOCTYPE html>
<html lang="en">
<head>
<meta charset="utf-8">
<title>TA BRAMLEY Business Card</title>
<link rel="stylesheet" href="https://fonts.googleapis.com/css2?family=Montserrat:wght@400;700&display=swap">
<style>
  :root {
    --brand-blue: #0f57a8;
    --card-white: #ffffff;
    --backdrop: #d9d9d6;
  }
  * { margin: 0; padding: 0; box-sizing: border-box; }
  html, body {
    width: 1200px; height: 801px; overflow: hidden;
    background: var(--backdrop);
    font-family: "Montserrat", sans-serif;
  }
  .stage { position: relative; width: 1200px; height: 801px; }
  .card {
    position: absolute; top: 246px;
    width: 540px; height: 309px;
    overflow: hidden;
    box-shadow: 0 10px 24px rgba(0,0,0,0.18);
  }
  .card--front { left: 40px; background: var(--brand-blue); }
  .card--back { left: 620px; background: var(--brand-blue); display: flex; align-items: center; justify-content: center; }
  .front-shape { position: absolute; inset: 0; }
  .brand-name {
    font-weight: 700; letter-spacing: 0.08em; white-space: nowrap;
  }
  .card--front .brand-name {
    position: absolute; right: 30px; top: 96px;
    color: var(--brand-blue); font-size: 20px;
  }
  .card--back .brand-name { color: var(--card-white); font-size: 52px; }
  .contact-block {
    position: absolute; left: 42px; top: 128px;
    color: var(--card-white);
  }
  .name-marker {
    position: absolute; left: 0; top: 131px;
    width: 24px; height: 28px; background: var(--card-white);
  }
  .person-name { font-weight: 700; font-size: 19px; letter-spacing: 0.03em; line-height: 1.1; }
  .person-title { font-size: 13px; margin-bottom: 14px; }
  .contact-line { display: flex; align-items: center; gap: 8px; font-size: 12.5px; line-height: 1.55; }
  .contact-line svg { width: 11px; height: 11px; fill: var(--card-white); flex: none; }
  .address { font-size: 12.5px; line-height: 1.45; margin-top: 12px; margin-left: 19px; }
</style>
</head>
<body>
<main class="stage">
  <section class="card card--front" aria-label="Business card front">
    <svg class="front-shape" viewBox="0 0 540 309" aria-hidden="true">
      <path d="M262,0 C292,18 306,110 334,180 C366,252 452,278 540,270 L540,0 Z" fill="#ffffff"/>
      <path d="M278,8 C304,40 314,120 342,178 C374,236 450,258 520,256" fill="none" stroke="#0f57a8" stroke-width="5"/>
      <path d="M262,0 C286,30 300,115 322,185 C352,262 460,290 540,280" fill="none" stroke="#ffffff" stroke-width="2"/>
    </svg>
    <div class="brand-name">TA BRAMLEY</div>
    <div class="name-marker"></div>
    <div class="contact-block">
      <div class="person-name">MARA QUINLAN</div>
      <div class="person-title">Managing Director</div>
      <div class="contact-line">
        <svg viewBox="0 0 12 12"><path d="M2,1 L4.5,1 L5.5,3.5 L4,4.5 C4.6,6 6,7.4 7.5,8 L8.5,6.5 L11,7.5 L11,10 C11,10.6 10.6,11 10,11 C5,11 1,7 1,2 C1,1.4 1.4,1 2,1 Z"/></svg>
        <span>123 456 789</span>
      </div>
      <div class="contact-line">
        <svg viewBox="0 0 12 12"><path d="M1,3 L11,3 L11,10 L1,10 Z M1.5,3.5 L6,7 L10.5,3.5" stroke="#0f57a8" stroke-width="0.8"/></svg>
        <span>hello@tabramley.com</span>
      </div>
      <div class="contact-line">
        <svg viewBox="0 0 12 12"><circle cx="6" cy="6" r="5"/></svg>
        <span>www.tabramley.com</span>
      </div>
      <div class="address">Your address, City<br>State, Zip 1234</div>
    </div>
  </section>
  <section class="card card--back" aria-label="Business card back">
    <div class="brand-name">TA BRAMLEY</div>
  </section>
</main>
</body>
</html>
```